PAX

We need to design a power point presentation that can englobe all our company products.

This presentation has to have all the required to be used as template for future presentations.

We focus on prodcut developing for supermarkets, ( we help them with their own brand products ex. Sunny Harvest, TK, etc.)
Also we are on the marine industry, we develop ships and oil rigs for the Oil and deep water market.

Target Market(s)

Oil Companies
Supermarket companies
Retail Companies

Industry/Entity Type

It Company

Requirements
Must have
• Our Logo and company colors
Nice to have
• Something describing globalization.
Should not have
• Orange color

```html
<!DOCTYPE html>
<html lang="en">
<head>
<meta charset="utf-8">
<title>PAX — Presentation Template</title>
<link rel="stylesheet" href="https://fonts.googleapis.com/css2?family=Orbitron:wght@500;800&family=Arimo:wght@400&display=swap">
<style>
  :root {
    --blue-deep: #0a2fb8;
    --blue-main: #1a4ef0;
    --blue-bright: #2f6bff;
    --green: #7cdc1e;
    --green-heading: #6ef01e;
    --white: #ffffff;
    --ring: #0b2a8c;
    --tab-white: #f4f6fa;
  }
  * { margin: 0; padding: 0; box-sizing: border-box; }
  html, body { width: 1200px; height: 900px; overflow: hidden; background: var(--blue-main); }
  .slide {
    position: relative;
    width: 1200px;
    height: 900px;
    overflow: hidden;
    background:
      repeating-linear-gradient(90deg, rgba(255,255,255,0.035) 0 2px, transparent 2px 9px),
      repeating-linear-gradient(0deg, rgba(255,255,255,0.035) 0 2px, transparent 2px 9px),
      radial-gradient(ellipse at 45% 45%, var(--blue-bright) 0%, var(--blue-main) 45%, var(--blue-deep) 100%);
  }
  .header-band { position: absolute; top: 0; left: 0; width: 1200px; height: 200px; }
  .title {
    position: absolute;
    top: 42px;
    left: 0;
    width: 1190px;
    text-align: center;
    font-family: 'Orbitron', sans-serif;
    font-weight: 800;
    font-size: 43px;
    letter-spacing: 3px;
    color: var(--white);
  }
  .logo-tab {
    position: absolute;
    top: 0;
    left: 1012px;
    width: 144px;
    height: 178px;
    border-radius: 0 0 30px 30px;
    background: linear-gradient(180deg, var(--white) 0%, var(--tab-white) 100%);
    box-shadow: 0 2px 10px rgba(0,0,40,0.35);
    display: flex;
    flex-direction: column;
    align-items: center;
    justify-content: center;
    gap: 14px;
  }
  .logo-dot { width: 54px; height: 54px; border-radius: 50%; background: var(--blue-main); }
  .logo-name {
    font-family: 'Orbitron', sans-serif;
    font-weight: 500;
    font-size: 36px;
    color: var(--green);
  }
  .content { position: absolute; left: 62px; width: 860px; }
  .section { position: absolute; left: 0; width: 860px; }
  .section-heading {
    font-family: 'Orbitron', sans-serif;
    font-weight: 500;
    font-size: 33px;
    letter-spacing: 1px;
    color: var(--green-heading);
    line-height: 40px;
  }
  .section-body {
    margin-top: 12px;
    font-family: 'Arimo', sans-serif;
    font-size: 21px;
    line-height: 36px;
    color: var(--white);
  }
  .photo {
    position: absolute;
    left: 994px;
    width: 172px;
    height: 172px;
    border-radius: 50%;
    border: 6px solid var(--ring);
    box-shadow: 0 0 0 2px rgba(60,120,255,0.6);
  }
  .photo-vessel { top: 262px; background: linear-gradient(180deg, #9ec3e8 0%, #c9d6e2 45%, #c4442e 70%, #2d5f8f 100%); }
  .photo-cruise { top: 475px; background: linear-gradient(180deg, #8fb6dc 0%, #dfe6ee 50%, #2e6aa8 75%, #1d4f86 100%); }
  .photo-rig { top: 691px; background: linear-gradient(180deg, #3a5d88 0%, #243650 55%, #121a24 100%); }
  .footer-band { position: absolute; left: 0; bottom: 0; width: 1200px; height: 15px; background: var(--green); }
</style>
</head>
<body>
<main class="slide">
  <svg class="header-band" viewBox="0 0 1200 200" aria-hidden="false">
    <defs>
      <linearGradient id="mapTone" x1="0" y1="0" x2="0" y2="1">
        <stop offset="0" stop-color="#4a86ff"/>
        <stop offset="1" stop-color="#1a4ed8"/>
      </linearGradient>
    </defs>
    <path role="img" aria-label="World map backdrop in light blue tones" d="M0 0 H1200 V0 Q380 260 0 45 Z" fill="url(#mapTone)"/>
    <path d="M0 45 Q380 260 1200 0" fill="none" stroke="var(--green)" stroke-width="5"/>
  </svg>

  <h1 class="title">PROJECT TITLE HERE</h1>

  <div class="logo-tab">
    <span class="logo-dot"></span>
    <span class="logo-name">PAX</span>
  </div>

  <div class="content">
    <section class="section" style="top:196px">
      <h2 class="section-heading">Content Heading Here</h2>
      <p class="section-body">Sub content here Sub content here Sub content here Sub content here Sub content here Sub content here Sub content here Sub content here Sub content here Sub content here Sub content here Sub content here</p>
    </section>
    <section class="section" style="top:422px">
      <h2 class="section-heading">Content Heading Here</h2>
      <p class="section-body">Sub content here Sub content here Sub content here Sub content here Sub content here Sub content here Sub content here Sub content here Sub content here Sub content here Sub content here Sub content here</p>
    </section>
    <section class="section" style="top:649px">
      <h2 class="section-heading">Content Heading Here</h2>
      <p class="section-body">Sub content here Sub content here Sub content here Sub content here Sub content here Sub</p>
    </section>
  </div>

  <div class="photo photo-vessel" role="img" aria-label="Photo of offshore supply vessels near an oil platform"></div>
  <div class="photo photo-cruise" role="img" aria-label="Photo of a white cruise ship at sea"></div>
  <div class="photo photo-rig" role="img" aria-label="Photo of an oil rig silhouette at dusk"></div>

  <div class="footer-band"></div>
</main>
</body>
</html>
```